Web Design Project for SEARCH ENGINE !

We need a website design for torrents search engine.

The Website will be www.Qentrova.com

Qentrova is a a search engine for torrents.
Qentrova search and index torrents results from all torrents sites.

We will need:
Logo
WebSite Design
slogen (optional)

we need only PSDs - no codded pages are needed !

Design to the following screen Size & resolution: 1024 x 768

***PLEASE DOWNLOAD ATTACHED FILE !

```html
<!DOCTYPE html>
<html lang="en">
<head>
<meta charset="utf-8">
<title>Qentrova – Torrents Search Engine</title>
<link rel="stylesheet" href="https://fonts.googleapis.com/css2?family=Source+Sans+3:wght@400;600;700&display=swap">
<style>
  :root{
    --green:#2fb54a;
    --green-bright:#39c84f;
    --dark:#1b1b1b;
    --dark-2:#3a3a3a;
    --grey-logo:#6d6e71;
    --grey-text:#444;
    --field:#e6e6e6;
    --page:#ffffff;
    --canvas:#f2f2f2;
    --white:#ffffff;
    --icon-muted:#b9c2cc;
  }
  *{box-sizing:border-box;margin:0;padding:0}
  html,body{width:1200px;height:567px;overflow:hidden;background:var(--page)}
  body{font-family:"Source Sans 3",Arial,sans-serif;color:var(--grey-text);position:relative}

  .stage{position:absolute;left:16px;top:12px;width:1168px;height:539px;
    background:linear-gradient(#f4f4f4 0%,#ffffff 25%,#ffffff 65%,#ececec 100%)}

  .dark-panel{position:absolute;background:linear-gradient(#3c3c3c,#141414 45%,#1f1f1f);
    box-shadow:0 3px 6px rgba(0,0,0,.35);color:var(--white)}
  .tab{position:absolute;width:12px;height:12px;border-radius:50%;background:var(--dark)}

  /* top navigation */
  .main-nav{left:191px;top:4px;width:817px;height:64px;border-radius:0 0 14px 14px;
    display:flex;align-items:center;padding-left:28px;font-size:17px;letter-spacing:.2px}
  .main-nav a{color:var(--white);text-decoration:none}
  .main-nav a.current{color:var(--green-bright)}
  .main-nav .sep{margin:0 11px;color:var(--white)}
  .lang{position:absolute;left:721px;top:19px;width:78px;height:25px;background:var(--green);
    color:var(--white);font-size:14px;display:flex;align-items:center;padding-left:9px}
  .lang svg{margin-left:9px}

  .social{position:absolute;top:30px;display:flex;gap:21px}
  .social span{width:21px;height:21px;border-radius:3px;background:var(--icon-muted);display:block}
  .social.left{left:29px}
  .social.right{left:1022px;gap:22px}

  /* side panels */
  .signup{left:4px;top:136px;width:166px;height:298px;border-radius:0 8px 8px 0;padding:10px 14px 0 14px}
  .login{left:1030px;top:129px;width:166px;height:190px;border-radius:8px 0 0 8px;padding:10px 14px 0 15px}
  .panel-title{color:var(--green-bright);font-size:12px;text-align:center;letter-spacing:.2px}
  .field-label{font-size:11.5px;margin-top:5px}
  .field{height:20px;background:linear-gradient(#f4f4f4,#dcdcdc);border-radius:3px;margin-top:2px;
    display:flex;align-items:center;padding-left:5px}
  .signup .field{margin-bottom:9px}
  .agree{font-size:8px;color:var(--green-bright);display:flex;align-items:center;gap:4px;margin-top:-2px;margin-left:10px}
  .box{width:8px;height:8px;background:#ddd;display:inline-block}
  .btn-small{display:block;margin-left:auto;margin-top:6px;background:linear-gradient(#fff,#cfcfcf);
    color:#333;font-size:10px;padding:2px 6px;border-radius:2px;width:max-content}
  .forgot{color:var(--green-bright);font-size:14px;text-align:center;margin-top:10px}
  .stats{left:1030px;top:352px;width:166px;height:71px;border-radius:8px 0 0 8px;text-align:center;padding-top:10px}
  .stats .panel-title{font-size:14px}
  .stats .count{font-size:26px;font-weight:600;margin-top:1px}

  /* brand */
  .brand{position:absolute;left:0;width:1200px;top:140px;text-align:center}
  .brand-name{display:inline-flex;align-items:center;gap:10px;font-size:74px;font-weight:700;color:var(--grey-logo);line-height:1}
  .brand-dot{width:56px;height:56px;border-radius:50%;background:var(--green)}
  .tagline{font-size:24px;color:var(--grey-logo);margin-top:4px;letter-spacing:.3px}

  /* search */
  .search{position:absolute;left:191px;top:297px;width:817px;height:37px;display:flex}
  .search-input{flex:1;background:var(--field);font-size:21px;color:#333;padding-left:9px;display:flex;align-items:center}
  .search-btn{width:73px;background:var(--dark);color:var(--white);font-size:11.5px;display:flex;align-items:center;justify-content:center;gap:3px}
  .search-opt{position:absolute;right:192px;top:340px;font-size:13px;display:flex;align-items:center;gap:4px}
  .check{width:12px;height:12px;border:1px solid #555;background:#eee}

  /* footer */
  .footer{left:191px;top:498px;width:817px;height:65px;border-radius:14px 14px 0 0;
    display:flex;align-items:center;justify-content:center;font-size:13.5px;letter-spacing:.1px}
  .footer a{color:var(--green-bright);text-decoration:none;margin:0 4px}
</style>
</head>
<body>
<div class="stage"></div>

<div class="tab" style="left:185px;top:-2px"></div>
<div class="tab" style="left:1003px;top:-2px"></div>
<div class="tab" style="left:-2px;top:114px"></div>
<div class="tab" style="left:-2px;top:427px"></div>
<div class="tab" style="left:1191px;top:106px"></div>
<div class="tab" style="left:1191px;top:312px"></div>
<div class="tab" style="left:1191px;top:336px"></div>
<div class="tab" style="left:1191px;top:428px"></div>
<div class="tab" style="left:169px;top:555px"></div>
<div class="tab" style="left:1018px;top:555px"></div>

<div class="social left"><span></span><span></span><span></span><span></span></div>
<div class="social right"><span></span><span></span><span></span><span></span></div>

<nav class="main-nav dark-panel">
  <a class="current" href="#">HOME</a><span class="sep">|</span>
  <a href="#">ABOUT US</a><span class="sep">|</span>
  <a href="#">TORRENT SEARCH</a><span class="sep">|</span>
  <a href="#">SITE SEARCH</a><span class="sep">|</span>
  <a href="#">HELP</a><span class="sep">|</span>
  <a href="#">LOGIN</a><span class="sep">|</span>
  <a href="#">SIGNIN</a>
  <div class="lang">English
    <svg width="9" height="7" viewBox="0 0 9 7"><path d="M0 0h9L4.5 7z" fill="#fff"/></svg>
  </div>
</nav>

<aside class="signup dark-panel">
  <div class="panel-title">MEMBER SIGNIN</div>
  <div class="field-label">Username</div>
  <div class="field"><svg width="10" height="11" viewBox="0 0 10 11"><circle cx="5" cy="3" r="2.6" fill="#222"/><path d="M0 11c0-4 10-4 10 0z" fill="#222"/></svg></div>
  <div class="field-label">Password</div>
  <div class="field"><svg width="11" height="11" viewBox="0 0 11 11"><circle cx="7.5" cy="3.5" r="3" fill="#333"/><path d="M6 5 1 10" stroke="#333" stroke-width="1.6"/></svg></div>
  <div class="field-label">Retype Password</div>
  <div class="field"><svg width="11" height="11" viewBox="0 0 11 11"><circle cx="7.5" cy="3.5" r="3" fill="#333"/><path d="M6 5 1 10" stroke="#333" stroke-width="1.6"/></svg></div>
  <div class="field-label">Email</div>
  <div class="field"><svg width="13" height="10" viewBox="0 0 13 10"><rect x=".5" y=".5" width="12" height="9" fill="none" stroke="#333"/><path d="M.5 .5 6.5 5.5 12.5 .5" fill="none" stroke="#333"/></svg></div>
  <div class="field-label">Retype Email</div>
  <div class="field"><svg width="13" height="10" viewBox="0 0 13 10"><rect x=".5" y=".5" width="12" height="9" fill="none" stroke="#333"/><path d="M.5 .5 6.5 5.5 12.5 .5" fill="none" stroke="#333"/></svg></div>
  <div class="agree"><span class="box"></span>AGREE TO PRIVACY POLICY</div>
  <span class="btn-small">SIGNIN</span>
</aside>

<aside class="login dark-panel">
  <div class="panel-title">MEMBER LOGIN</div>
  <div class="field-label">Username</div>
  <div class="field"><svg width="10" height="11" viewBox="0 0 10 11"><circle cx="5" cy="3" r="2.6" fill="#222"/><path d="M0 11c0-4 10-4 10 0z" fill="#222"/></svg></div>
  <div class="field-label" style="margin-top:9px">Password</div>
  <div class="field"><svg width="11" height="11" viewBox="0 0 11 11"><circle cx="7.5" cy="3.5" r="3" fill="#333"/><path d="M6 5 1 10" stroke="#333" stroke-width="1.6"/></svg></div>
  <div class="forgot">FORGET PASWORD?</div>
  <span class="btn-small">LOGIN</span>
</aside>

<aside class="stats dark-panel">
  <div class="panel-title">CURRENT TORRENTS</div>
  <div class="count">283.666</div>
</aside>

<header class="brand">
  <div class="brand-name"><span class="brand-dot"></span>Qentrova</div>
  <div class="tagline">TORRENTS SEARCH ENGINE</div>
</header>

<form class="search">
  <div class="search-input">starbound 3</div>
  <div class="search-btn">
    <svg width="11" height="11" viewBox="0 0 11 11"><circle cx="4.5" cy="4.5" r="3.3" fill="none" stroke="#fff" stroke-width="1.5"/><path d="M7 7l3.3 3.3" stroke="#fff" stroke-width="1.8"/></svg>SEARCH
  </div>
</form>
<div class="search-opt">Sites search include
  <svg class="check" viewBox="0 0 12 12"><path d="M2 6l3 3 5-6" fill="none" stroke="#333" stroke-width="1.5"/></svg>
</div>

<footer class="footer dark-panel">
  COPYRIGHT © 2011 QENTROVA. USE OF THIS WEBSITE CONSTITUTES ACCEPTANCE OF OUR
  <a href="#">USER AGREEMENT</a> AND <a href="#">PRIVACY POLICY</a>.
</footer>
</body>
</html>
```